Harborlane Products Flyer

Harborlane Lending Group, Inc.
Licensed Mortgage Company
Serving the DMV since 1997
"You open the Harborlane, we'll carry the load"
We specialize in...
FHA Loans
* Credit Scores as low as 500
* 203K Renovation Loans
Conventional Loans
* As little as 1% Down
* Bank Statement for Self-Employed
Investor Loans
* DSCR, & Fix & Flip
* Commercial & New Construction
Other Programs
* HELOCS & Reverse Mortgages
Call today for a free consultation
(800) 914-6027
www.harborlanehomeloans.com
NMLS #731860

```html
<!DOCTYPE html>
<html lang="en">
<head>
<meta charset="utf-8">
<title>Harborlane Products Flyer</title>
<link href="https://fonts.googleapis.com/css2?family=Montserrat:wght@800&family=Fira+Sans:wght@600;700&family=Open+Sans:wght@400;700&display=swap" rel="stylesheet">
<style>
  :root{
    --page:#b9d9f8;
    --navy:#07151f;
    --gold-light:#f3e3bf;
    --gold:#e3bb6a;
    --gold-deep:#c98a2c;
    --blue:#1f5fc6;
    --blue-bright:#2f74d9;
    --blue-deep:#0f34a0;
    --ink:#1b1b1b;
    --white:#ffffff;
  }
  *{margin:0;padding:0;box-sizing:border-box}
  html,body{width:928px;height:1200px;overflow:hidden;background:var(--page)}
  .flyer{position:absolute;left:109px;top:98px;width:710px;height:1004px;background:var(--navy);overflow:hidden;font-family:"Open Sans",sans-serif}
  .hero-photo{position:absolute;left:276px;top:0;width:434px;height:364px;
    background:linear-gradient(180deg,#3c4a3a 0%,#5d6e4c 45%,#3f6a2e 80%,#22331f 100%);
    -webkit-mask-image:linear-gradient(90deg,transparent 0%,#000 35%,#000 100%);
    mask-image:linear-gradient(90deg,transparent 0%,#000 35%,#000 100%)}
  .hero-fade{position:absolute;left:276px;top:264px;width:434px;height:100px;background:linear-gradient(180deg,rgba(7,21,31,0),var(--navy))}
  .nmls{position:absolute;right:23px;top:14px;color:var(--white);font-size:16px;z-index:3}
  .brand{position:absolute;left:44px;top:62px;width:210px;text-align:center;z-index:3}
  .brand-mark{width:30px;height:30px;border-radius:50%;background:var(--gold);margin:0 auto 8px}
  .brand-name{font-weight:700;font-size:17px;color:var(--gold);line-height:1.15}
  .brand-tag{font-size:7.5px;color:#8fb2ee;margin-top:4px}
  .brand-est{font-size:8px;color:var(--white);letter-spacing:1.5px;margin-top:3px}
  .headline{position:absolute;left:46px;top:203px;z-index:3;font-family:"Montserrat",sans-serif;font-weight:800;font-size:42px;line-height:50px;white-space:nowrap;
    background:linear-gradient(90deg,var(--gold) 0%,var(--gold-light) 45%,var(--gold-deep) 100%);-webkit-background-clip:text;background-clip:text;color:transparent}
  .lower-photo{position:absolute;left:0;top:375px;width:710px;height:580px;background:radial-gradient(ellipse at 50% 45%,#34404a 0%,#1e2b35 55%,#121f29 100%)}
  .frame{position:absolute;left:0;top:0}
  .pill{position:absolute;left:221px;top:458px;width:268px;height:36px;border-radius:18px;background:linear-gradient(90deg,var(--blue-bright),var(--blue-deep));
    color:var(--white);font-family:"Montserrat",sans-serif;font-weight:800;font-size:20px;text-align:center;line-height:36px}
  .card{position:absolute;width:283px;height:137px;background:var(--white);border-radius:8px;border:1px solid #d6e3f5;padding:18px 0 0 14px}
  .card h2{font-family:"Fira Sans",sans-serif;font-weight:700;font-size:21px;color:var(--blue);line-height:1}
  .card ul{list-style:none;margin-top:10px}
  .card li{position:relative;padding-left:27px;font-size:15.5px;color:var(--ink);line-height:19px;margin-bottom:8px}
  .card li svg{position:absolute;left:0;top:2px}
  .card .icon{position:absolute;right:10px;bottom:8px}
  .fha{left:59px;top:525px}
  .conv{left:368px;top:525px}
  .inv{left:59px;top:688px}
  .other{left:368px;top:688px}
  .conv ul{margin-top:13px}
  .cta{position:absolute;left:0;top:905px;width:710px;height:90px;text-align:center;color:var(--white)}
  .cta-call{font-family:"Fira Sans",sans-serif;font-weight:600;font-size:20px;position:absolute;top:0;width:100%;line-height:26px}
  .cta-contacts{position:absolute;top:34px;width:100%;display:flex;justify-content:center;align-items:center;gap:10px;font-family:"Fira Sans",sans-serif;font-weight:700;font-size:23px}
  .gold-text{background:linear-gradient(90deg,var(--gold),var(--gold-deep));-webkit-background-clip:text;background-clip:text;color:transparent}
</style>
</head>
<body>
<main class="flyer">
  <div class="hero-photo" role="img" aria-label="Photo of a smiling family of four cheering in front of their new house, holding a home for sale sign"></div>
  <div class="hero-fade"></div>
  <p class="nmls">NMLS #731860</p>

  <div class="brand">
    <div class="brand-mark"></div>
    <p class="brand-name">Harborlane Lending Group</p>
    <p class="brand-tag">You open the Harborlane, we'll carry the load</p>
    <p class="brand-est">EST. 1997</p>
  </div>

  <h1 class="headline">YOU OPEN THE<br>HARBORLANE, WE'LL<br>CARRY THE LOAD</h1>

  <div class="lower-photo" role="img" aria-label="Faint background photo of a smiling family close together"></div>

  <svg class="frame" width="710" height="1004" viewBox="0 0 710 1004">
    <defs>
      <linearGradient id="roofGold" x1="0" x2="1">
        <stop offset="0" stop-color="#e8c27a"/><stop offset="0.4" stop-color="#f6ead0"/><stop offset="1" stop-color="#c98a2c"/>
      </linearGradient>
      <linearGradient id="ctaBlue" x1="0" x2="1">
        <stop offset="0" stop-color="#2f74d9"/><stop offset="1" stop-color="#0f34a0"/>
      </linearGradient>
    </defs>
    <polygon points="0,375 365,375 0,512" fill="#07151f"/>
    <polygon points="365,375 710,375 710,510" fill="#07151f"/>
    <polygon points="0,502 365,375 710,500 710,511 365,381 0,514" fill="url(#roofGold)"/>
    <polygon points="0,929 357,855 710,930 710,1004 0,1004" fill="url(#ctaBlue)"/>
    <polyline points="0,929 357,855 710,930" fill="none" stroke="#ffffff" stroke-width="4"/>
  </svg>

  <div class="pill">WE SPECIALIZE IN...</div>

  <section class="card fha">
    <h2>FHA Loans</h2>
    <ul>
      <li><svg width="18" height="18" viewBox="0 0 18 18"><circle cx="8" cy="10" r="7" fill="none" stroke="#1b1b1b" stroke-width="1.8"/><path d="M4.5 9.5l3 3L16 3" fill="none" stroke="#1b1b1b" stroke-width="2"/></svg>Credit Scores as low as <b>500</b></li>
      <li><svg width="18" height="18" viewBox="0 0 18 18"><circle cx="8" cy="10" r="7" fill="none" stroke="#1b1b1b" stroke-width="1.8"/><path d="M4.5 9.5l3 3L16 3" fill="none" stroke="#1b1b1b" stroke-width="2"/></svg>203K Renovation Loans</li>
    </ul>
    <svg class="icon" width="52" height="52" viewBox="0 0 52 52" fill="none" stroke="#1f5fc6" stroke-width="2"><path d="M4 18L18 6l14 12M8 15v33h14"/><rect x="13" y="18" width="9" height="9"/><path d="M22 34l14-11 14 11M26 31v17h20V31"/><rect x="34" y="39" width="5" height="9"/></svg>
  </section>

  <section class="card conv">
    <h2>Conventional Loans</h2>
    <ul>
      <li><svg width="18" height="18" viewBox="0 0 18 18"><circle cx="8" cy="10" r="7" fill="none" stroke="#1b1b1b" stroke-width="1.8"/><path d="M4.5 9.5l3 3L16 3" fill="none" stroke="#1b1b1b" stroke-width="2"/></svg>As little as <b>1% Down</b></li>
      <li><svg width="18" height="18" viewBox="0 0 18 18"><circle cx="8" cy="10" r="7" fill="none" stroke="#1b1b1b" stroke-width="1.8"/><path d="M4.5 9.5l3 3L16 3" fill="none" stroke="#1b1b1b" stroke-width="2"/></svg>Bank Statement for<br>Self-Employed</li>
    </ul>
    <svg class="icon" width="54" height="54" viewBox="0 0 54 54" fill="none" stroke="#1f5fc6" stroke-width="2"><circle cx="27" cy="26" r="12"/><path d="M30 21h-5a3 3 0 000 6h4a3 3 0 010 6h-5M27 18v18"/><path d="M2 36h4v16H2zM6 46h20l14-8M44 2h4v16h-4zM44 8H28l-14 8"/></svg>
  </section>

  <section class="card inv">
    <h2>Investor Loans</h2>
    <ul>
      <li><svg width="18" height="18" viewBox="0 0 18 18"><circle cx="8" cy="10" r="7" fill="none" stroke="#1b1b1b" stroke-width="1.8"/><path d="M4.5 9.5l3 3L16 3" fill="none" stroke="#1b1b1b" stroke-width="2"/></svg>DSCR, &amp; Fix &amp; Flip</li>
      <li><svg width="18" height="18" viewBox="0 0 18 18"><circle cx="8" cy="10" r="7" fill="none" stroke="#1b1b1b" stroke-width="1.8"/><path d="M4.5 9.5l3 3L16 3" fill="none" stroke="#1b1b1b" stroke-width="2"/></svg>Commercial &amp;<br>New Construction</li>
    </ul>
    <svg class="icon" width="52" height="58" viewBox="0 0 52 58" fill="none" stroke="#1f5fc6" stroke-width="2"><path d="M2 8h46M14 2v54M20 2v54M14 56h8M48 8v12"/><rect x="30" y="26" width="20" height="30"/><rect x="34" y="32" width="5" height="5"/><rect x="42" y="32" width="5" height="5"/><rect x="34" y="44" width="5" height="5"/><rect x="42" y="44" width="5" height="5"/></svg>
  </section>

  <section class="card other">
    <h2>Other Programs</h2>
    <ul>
      <li><svg width="18" height="18" viewBox="0 0 18 18"><circle cx="8" cy="10" r="7" fill="none" stroke="#1b1b1b" stroke-width="1.8"/><path d="M4.5 9.5l3 3L16 3" fill="none" stroke="#1b1b1b" stroke-width="2"/></svg>HELOCS &amp; Reverse<br>Mortgages</li>
    </ul>
    <svg class="icon" width="58" height="58" viewBox="0 0 58 58" fill="none" stroke="#1f5fc6" stroke-width="2"><path d="M10 30V2h38v54H30"/><path d="M18 10h24M18 16h24M18 22h24M18 28h24"/><path d="M2 44l12-10 12 10M5 42v14h18V42"/><circle cx="38" cy="46" r="9"/><path d="M40 42h-3a2 2 0 000 4h2a2 2 0 010 4h-3M38 39v14"/></svg>
  </section>

  <footer class="cta">
    <p class="cta-call">Call today for a free consultation</p>
    <div class="cta-contacts">
      <svg width="24" height="24" viewBox="0 0 24 24" fill="none" stroke="#e3bb6a" stroke-width="1.8"><path d="M5 3l4 4-2 3c1.5 3 4 5.5 7 7l3-2 4 4-3 3C10 22 2 14 2 6z"/><path d="M14 2a8 8 0 018 8M14 6a4 4 0 014 4"/></svg>
      <span class="gold-text">(800) 914-6027</span>
      <svg width="24" height="24" viewBox="0 0 24 24" fill="none" stroke="#e3bb6a" stroke-width="1.6"><circle cx="12" cy="12" r="10"/><ellipse cx="12" cy="12" rx="4.5" ry="10"/><path d="M2 12h20M4 6h16M4 18h16"/></svg>
      <span class="gold-text">www.harborlanehomeloans.com</span>
    </div>
  </footer>
</main>
</body>
</html>
```